Snoutsaver.net Dog Coupon Site Website Design

TailThrift - Dog Coupon Site Design Brief

Project Overview
**Site Name:** SnoutSaver.net
**Purpose:** A modern coupon aggregation platform specifically for dog and pet-related products and services
**Target Audience:** Dog owners, pet enthusiasts, budget-conscious pet parents

Brand Identity & Visual Direction

Typography
- **Headers:** Modern sans-serif (Inter or similar) - Clean and friendly
- **Body:** Readable sans-serif with good mobile legibility
- **Accent:** Playful but professional font for coupon codes

Design Principles
- **Flat Design:** Clean, minimal with subtle shadows
- **Friendly & Approachable:** Rounded corners, soft edges
- **Trust-Building:** Clear pricing, transparent savings
- **Scannable:** Easy-to-read coupon codes and offers

## User Experience & Functionality

### Homepage Features
1. **Hero Section**
- Clear value proposition
- Search functionality
- Featured savings highlight

2. **Coupon Cards**
- One-click copy functionality
- Clear discount display
- Store/brand logos
- Expiration dates
- "Get Deal" call-to-action

3. **Navigation**
- Categories (Food, Toys, Health, Services, etc.)
- Popular stores
- Latest deals

### Interactive Elements
- **Copy Button:** Instant feedback when coupon copied
- **Deal Pages:** Detailed offer information, terms, store details
- **Search & Filter:** By category, store, discount amount
- **Mobile Menu:** Hamburger navigation for mobile

## Technical Requirements

### Responsive Design
- **Mobile-First:** Optimized for touch interactions
- **Tablet:** Adapted layout for medium screens
- **Desktop:** Full-width utilization with sidebar potential

### Performance
- **Fast Loading:** Optimized images, minimal JavaScript
- **Accessibility:** WCAG compliant, screen reader friendly
- **SEO Optimized:** Structured data for deals and offers

## Content Strategy

### Deal Categories
- Dog Food & Treats
- Toys & Accessories
- Health & Grooming
- Training & Services
- Outdoor & Travel

### Key Messaging
- "Save on everything your dog loves"
- "Verified deals updated daily"
- "Your pup deserves the best for less"

## Conversion Optimization

### Trust Elements
- Deal verification badges
- User reviews/ratings
- Clear savings calculations
- Expiration date transparency

### Call-to-Actions
- "Copy Code" (primary action)
- "Get Deal" (secondary action)
- "View All [Store] Deals"

## Success Metrics
- Coupon copy rate
- Click-through to retailer
- User return visits
- Mobile vs desktop usage
- Category performance

This design brief ensures a user-friendly, trustworthy platform that makes finding and using pet deals effortless while maintaining a warm, dog-loving community feel.

1. Design Objective
Create a warm, energetic space where dog lovers instantly feel welcomed and confident they’re finding genuine savings for their furry friends. Everything from the layout to the smallest icon should reinforce trust, delight, and simplicity.
2. Visual Personality
Color Palette: Soft, cheerful hues—think warm yellows and gentle blues—that evoke sunshine and playfulness without overwhelming.
Typography:
Headings: A modern, friendly sans‑serif (like Inter) with open letterforms to feel approachable.
Body Copy: Highly legible sans‑serif with generous line spacing for comfort on small screens.
Accent Font: A slightly quirky, hand‑drawn style used sparingly for coupon codes and special call‑outs, giving a personal, “paw‑picked” touch.
Imagery & Icons: Real‑life photographs of happy dogs interspersed with clean line‑icons of bones, paw prints, and hearts. Rounded shapes and subtle shadows keep the look soft and contemporary.
3. Layout & Hierarchy
Hero Area:
Full‑bleed image of a joyful dog, overlaid with a single, punchy tagline (“Save on everything your dog loves”).
Prominent search bar centered to invite exploration.
Offer Grid:
Generous white space around each coupon card so the eye can rest and scan easily.
Coupon cards feature a bold discount label, brand logo, and a friendly “Get Deal” button.
A playful “Copied!” animation briefly replaces the button once the code is grabbed.
Navigation:
A fixed header with clear category labels (Food, Toys, Health, Services).
A secondary “Popular Stores” carousel below to spotlight key partners.
4. Interaction & Motion
Micro‑interactions:
Hover state for cards subtly lifts the card and deepens its shadow, inviting a click.
Copy‑code button pulses once on hover, hinting at its one‑click magic.
Transitions:
Smooth fades between deal filters and search results to reassure users that the site is responding.
Loading indicators shaped like spinning collars or wagging tails to keep the theme consistent.
5. Accessibility & Inclusivity
Ensure all text meets contrast standards so every pet parent—regardless of vision—can read offers with ease.
Interactive elements sized for easy tapping on touchscreens.
Alt‑text for all imagery describing dogs, products, and actions for screen‑reader users.
6. Emotional Tone
From the moment someone lands on SnoutSaver.net, they should feel the joy of treating their dog without guilt. Friendly copy (“Your pup deserves the best for less”) paired with bright visuals will create a sense of community and shared passion.
7. Success by Design
Scan‑ability: Users should spot great deals in under two seconds.
Trust Signals: Badges (“Verified Savings”), clear expiration dates, and reviewer star icons should feel earned and prominent.
Return Visits: A “My Favorite Deals” heart icon encourages saving and returning, reinforced by subtle reminders in the UI.
This design approach keeps dog lovers front and center—making sure every graphic, font choice, and interaction feels like it was lovingly tailored for them.

Target Market(s)

Dog Lovers looking for good deals

Industry/Entity Type

Coupon Code

Number of Pages Required

4 page

Font styles to use
Sans Serif

Requirements
Must have
• Modern look, coupon copy cards it's a deal site and I want the coupon code and copy in the coupon card, blog section, review section, modern footer/header
Nice to have
• Modern coupon code website, easy to use

```html
<!DOCTYPE html>
<html lang="en">
<head>
<meta charset="utf-8">
<title>SnoutSaver.net — Save on Everything Your Dog Loves</title>
<link rel="stylesheet" href="https://fonts.googleapis.com/css2?family=Inter:wght@400;500;600;700;800&family=Lato:wght@400;700&display=swap">
<style>
:root{
  --blue:#0b86da;
  --blue-dark:#0a6fb8;
  --yellow:#ffe51a;
  --yellow-soft:#fff07a;
  --sky:#d9edfb;
  --ink:#141414;
  --muted:#4a4a4a;
  --grey-btn:#8d8d8d;
  --card-blue:#bcd7e6;
  --footer:#0b1320;
  --white:#fff;
}
*{box-sizing:border-box;margin:0;padding:0}
html,body{width:1200px;height:3771px;overflow:hidden;background:var(--white);font-family:"Lato",sans-serif;color:var(--ink)}
.page{position:relative;width:1200px;height:3771px}
.abs{position:absolute}
.btn-yellow{background:var(--yellow);border-radius:30px;font-family:"Inter",sans-serif;font-weight:700;color:var(--ink);display:flex;align-items:center;justify-content:center}
.section-title{position:absolute;left:0;width:1200px;text-align:center;font-family:"Inter",sans-serif;font-weight:500;font-size:44px;letter-spacing:.5px}
.section-title b{color:var(--blue);font-weight:700}
.section-sub{position:absolute;left:0;width:1200px;text-align:center;font-size:20px;color:#222}
.arrow{position:absolute;width:30px;height:30px;border-radius:50%;display:flex;align-items:center;justify-content:center}
.arrow.blue{background:var(--blue)}
.arrow.grey{background:#6b6b6b}

/* header */
.site-header{top:0;left:0;width:1200px;height:68px;background:#fff;box-shadow:0 1px 4px rgba(0,0,0,.08)}
.brand{left:110px;top:12px;display:flex;align-items:center;gap:12px;font-family:"Inter",sans-serif;font-size:25px;font-weight:500}
.brand-mark{width:42px;height:30px;border-radius:6px;background:var(--yellow)}
.brand b{color:var(--blue);font-weight:700}
.nav{left:608px;top:23px;display:flex;gap:25px;font-family:"Inter",sans-serif;font-size:15px;color:#222}
.contact-btn{left:955px;top:11px;width:133px;height:46px;font-size:17px}

/* hero */
.hero{top:68px;left:0;width:1200px;height:532px;background:linear-gradient(180deg,#6f8f3a 0%,#8fae4b 30%,#a7c059 55%,#7a9b35 80%,#5d7f22 100%)}
.hero-dog{left:40px;top:40px;width:480px;height:470px;border-radius:40%;background:radial-gradient(ellipse at center,rgba(222,170,110,.85),rgba(190,140,80,.35) 55%,transparent 72%)}
.hero-title{left:555px;top:112px;font-family:"Inter",sans-serif;font-weight:800;font-size:53px;line-height:61px;color:#fff;text-shadow:0 2px 6px rgba(0,0,0,.3)}
.hero-title span{color:#3aa3ff}
.get-started{left:557px;top:260px;width:136px;height:47px;font-size:17px}
.search-bar{left:333px;top:344px;width:532px;height:58px;background:#fff;border-radius:30px;box-shadow:0 2px 8px rgba(0,0,0,.15);display:flex;align-items:center;padding:0 20px;gap:20px}
.select{height:34px;border:1.5px solid #b9b9b9;border-radius:20px;display:flex;align-items:center;justify-content:space-between;padding:0 12px;font-size:12.5px;color:#777;font-family:"Inter",sans-serif}
.search-btn{width:30px;height:30px;border-radius:50%;background:var(--yellow);display:flex;align-items:center;justify-content:center;margin-left:12px}

/* coupons */
.coupon{top:797px;width:232px;height:315px;background:#fff;border-radius:14px;box-shadow:0 2px 10px rgba(0,0,0,.18);text-align:center;padding-top:14px}
.coupon.active{border:2px solid var(--yellow);top:784px;height:330px;padding-top:26px}
.ticket{margin:0 auto;width:156px;height:92px;background:var(--blue);position:relative;
  -webkit-mask:radial-gradient(circle 6px at 0 12px,transparent 98%,#000) 0 0/100% 24px repeat-y left,radial-gradient(circle 6px at 100% 12px,transparent 98%,#000) 0 0/100% 24px repeat-y right;
  -webkit-mask-size:51% 24px;-webkit-mask-repeat:repeat-y;-webkit-mask-position:left,right;
  mask:radial-gradient(circle 6px at 0 12px,transparent 98%,#000) left/51% 24px repeat-y,radial-gradient(circle 6px at 100% 12px,transparent 98%,#000) right/51% 24px repeat-y}
.ticket-label{padding-top:14px;color:#fff;font-family:"Inter",sans-serif;font-weight:800;font-size:19px;letter-spacing:.5px}
.ticket-off{margin:8px auto 0;width:96px;height:26px;border-radius:14px;background:#fff;font-family:"Inter",sans-serif;font-weight:800;font-size:16px;line-height:26px;color:var(--ink)}
.coupon h3{margin-top:18px;font-family:"Inter",sans-serif;font-weight:700;font-size:17px}
.coupon p{margin:8px auto 0;width:196px;font-size:11.5px;line-height:20px;color:#333}
.coupon .btn{margin:10px auto 0;width:144px;height:34px;display:flex;align-items:center;justify-content:center;gap:8px;font-family:"Inter",sans-serif;font-size:17px}
.btn.deal{background:var(--yellow-soft)}
.btn.copy{background:#bfe0f6;margin-top:13px}
.btn.copied{background:var(--grey-btn);color:#eee;margin-top:13px}
.btn.copy-live{background:var(--blue);color:#fff;margin-top:13px}

/* categories */
.band{left:0;width:1200px;background:var(--sky)}
.cat-card{top:1390px;width:304px;height:348px;background:#fff;box-shadow:0 2px 8px rgba(0,0,0,.15)}
.cat-img{margin:7px;height:283px}
.cat-card h3{text-align:center;font-family:"Inter",sans-serif;font-weight:700;font-size:22px;margin-top:12px}

/* stores */
.store{top:1962px;width:180px;height:102px;background:#fff;border-radius:14px;box-shadow:0 2px 9px rgba(0,0,0,.18);display:flex;align-items:center;justify-content:center;gap:8px;font-family:"Inter",sans-serif;font-weight:800;font-size:22px}
.store i{width:14px;height:14px;display:block}
.view-all{left:522px;top:2100px;width:153px;height:48px;font-size:17px}

/* testimonials */
.review{top:2385px;width:470px;height:240px;background:#fff;border-radius:22px;box-shadow:0 2px 8px rgba(0,0,0,.12)}
.avatar{left:16px;top:28px;width:80px;height:80px;border-radius:50%;background:linear-gradient(135deg,#a77a55,#6e8a5d)}
.review .name{left:114px;top:30px;font-family:"Inter",sans-serif;font-size:17px}
.review .lead{left:114px;top:56px;font-size:15.5px;color:var(--blue)}
.review .rating{left:114px;top:83px;display:flex;align-items:center;gap:10px;color:var(--yellow);font-size:13px;letter-spacing:2px}
.review .rating i{width:14px;height:14px;border-radius:50%;border:2.5px solid var(--blue);display:block}
.review .quote-mark{right:40px;top:20px;color:var(--blue);font-family:"Inter",sans-serif;font-size:40px;font-weight:800;line-height:1}
.review .text{left:18px;width:434px;font-size:12.7px;line-height:24px;color:#444;text-align:justify}

/* latest deals */
.deal-img{top:2866px;width:230px;height:244px;background:var(--card-blue);border-radius:4px}
.deal-img.active{border:2px solid var(--yellow)}
.deal-pct{left:14px;top:18px;display:flex;align-items:center;gap:8px;font-family:"Inter",sans-serif;font-size:21px}
.deal-pct i{width:26px;height:26px;border-radius:6px;background:var(--blue);display:block}
.deal-tag{right:12px;top:20px;padding:0 14px;height:30px;border-radius:16px;background:var(--yellow);font-family:"Inter",sans-serif;font-size:17px;line-height:30px}
.deal-art{left:30px;top:80px;width:170px;height:140px;border-radius:20px}
.deal-icons{right:12px;top:12px;display:flex;flex-direction:column;gap:8px}
.deal-icons span{width:26px;height:26px;border-radius:50%;background:#fff;display:flex;align-items:center;justify-content:center}
.deal-info{top:3150px;width:230px;font-family:"Inter",sans-serif}
.deal-info h4{font-size:14px;font-weight:700}
.deal-info .kind{font-size:14px;margin-top:7px;color:#222}
.deal-info .stars{color:#f2a20c;font-size:11px;letter-spacing:1px;margin-top:5px}
.deal-info .price{margin-top:7px;font-weight:700;font-size:15px;display:flex;align-items:baseline;gap:14px}
.deal-info .price s{font-weight:400;font-size:10.5px;color:#666}
.view-deals{left:510px;top:3284px;width:179px;height:47px;font-size:17px}

/* footer */
.site-footer{left:0;top:3415px;width:1200px;height:356px;background:var(--footer);color:#fff}
.f-brand{left:110px;top:88px;display:flex;align-items:center;gap:10px;font-family:"Inter",sans-serif;font-size:35px;font-weight:500}
.f-brand .brand-mark{width:60px;height:40px}
.f-brand b{color:var(--blue);font-weight:700}
.socials{left:146px;top:155px;display:flex;gap:11px}
.socials span{width:28px;height:28px;border-radius:50%;background:#fff;display:block}
.socials span:first-child{background:var(--blue)}
.f-col{top:88px;font-family:"Inter",sans-serif}
.f-col h5{color:var(--blue);font-size:17px;font-weight:500;margin-bottom:9px}
.f-col ul{list-style:none}
.f-col li{font-size:14.5px;line-height:34px;display:flex;align-items:center;gap:12px}
.f-col li::before{content:"";width:7px;height:7px;border-radius:50%;background:var(--blue)}
.f-col.contact li::before{display:none}
.f-col.contact li{align-items:flex-start;line-height:34px}
.ci{width:22px;height:22px;border-radius:50%;background:var(--blue);flex:none;margin-top:6px;display:flex;align-items:center;justify-content:center}
.f-rule{left:110px;top:310px;width:978px;height:1px;background:#38404d}
.copyright{left:0;top:326px;width:1200px;text-align:center;font-size:14px}
</style>
</head>
<body>
<div class="page">

<header class="site-header abs">
  <div class="brand abs"><span class="brand-mark"></span><span>Snout <b>Saver</b></span></div>
  <nav class="nav abs"><span>Categories</span><span>Popular Stores</span><span>Latest Deals</span></nav>
  <div class="contact-btn btn-yellow abs">Contact Us</div>
</header>

<section class="hero abs">
  <div class="hero-dog abs" role="img" aria-label="Golden dog leaping for a tennis ball over a sunny meadow"></div>
  <h1 class="hero-title abs">Save on Everything<br>Your <span>Dog Loves</span></h1>
  <div class="get-started btn-yellow abs">Get Started</div>
  <div class="search-bar abs">
    <div class="select" style="width:128px">By Category <svg width="10" height="6"><path d="M1 1l4 4 4-4" stroke="#777" fill="none" stroke-width="1.4"/></svg></div>
    <div class="select" style="width:128px">Store <svg width="10" height="6"><path d="M1 1l4 4 4-4" stroke="#777" fill="none" stroke-width="1.4"/></svg></div>
    <div class="select" style="width:140px">Discount Amount <svg width="10" height="6"><path d="M1 1l4 4 4-4" stroke="#777" fill="none" stroke-width="1.4"/></svg></div>
    <div class="search-btn"><svg width="18" height="18"><circle cx="8" cy="8" r="6" stroke="#222" stroke-width="1.6" fill="none"/><path d="M12.5 12.5l4 4" stroke="#222" stroke-width="1.6"/></svg></div>
  </div>
</section>

<h2 class="section-title" style="top:662px">Coupon <b>Cards</b></h2>
<p class="section-sub" style="top:731px">Your pup deserves the best for less</p>
<div class="arrow blue" style="left:42px;top:893px"><svg width="10" height="12"><path d="M7 1L2 6l5 5" stroke="#fff" stroke-width="2" fill="none"/></svg></div>
<div class="arrow grey" style="left:1131px;top:893px"><svg width="10" height="12"><path d="M3 1l5 5-5 5" stroke="#fff" stroke-width="2" fill="none"/></svg></div>

<article class="coupon abs" style="left:110px">
  <div class="ticket"><div class="ticket-label">COUPON</div><div class="ticket-off">20% OFF</div></div>
  <h3>Pawfect Pantry</h3>
  <p>Up to 20% Off: Sitewide discount on all orders.<br>Expiry Date 27.8.25</p>
  <div class="btn deal"><svg width="16" height="16"><path d="M2 8l7-7h6v6l-7 7z" fill="#222"/></svg>Get Deals</div>
  <div class="btn copy"><svg width="16" height="16"><path d="M2 8l7-7h6v6l-7 7z" fill="#222"/></svg>Copy Code</div>
</article>
<article class="coupon abs" style="left:358px">
  <div class="ticket"><div class="ticket-label">COUPON</div><div class="ticket-off">50% OFF</div></div>
  <h3>Wagly</h3>
  <p>Up to 50% Off + Extra 5% Off: Use code PUPPY5 on orders above<br>Expiry Date 27.8.25</p>
  <div class="btn deal"><svg width="16" height="16"><path d="M2 8l7-7h6v6l-7 7z" fill="#222"/></svg>Get Deals</div>
  <div class="btn copied"><svg width="16" height="16"><path d="M2 8l7-7h6v6l-7 7z" fill="#333"/></svg>Copied</div>
</article>
<article class="coupon active abs" style="left:600px;width:248px">
  <div class="ticket"><div class="ticket-label">COUPON</div><div class="ticket-off">10 % OFF</div></div>
  <h3>Furrow Shop</h3>
  <p>Extra 10% Off: Use code SNOUT10 on orders above ₹499.<br>Expiry Date 27.8.25</p>
  <div class="btn deal"><svg width="16" height="16"><path d="M2 8l7-7h6v6l-7 7z" fill="#222"/></svg>Get Deals</div>
  <div class="btn copy-live"><svg width="16" height="16"><path d="M2 8l7-7h6v6l-7 7z" fill="var(--yellow)"/></svg>Copy Code</div>
</article>
<article class="coupon abs" style="left:856px">
  <div class="ticket"><div class="ticket-label">COUPON</div><div class="ticket-off">15 % OFF</div></div>
  <h3>Maple Pet Store</h3>
  <p>Up to 15% Off: On dog toys including squeaker and chew toys.<br>Expiry Date 27.8.25</p>
  <div class="btn deal"><svg width="16" height="16"><path d="M2 8l7-7h6v6l-7 7z" fill="#222"/></svg>Get Deals</div>
  <div class="btn copy"><svg width="16" height="16"><path d="M2 8l7-7h6v6l-7 7z" fill="#222"/></svg>Copy Code</div>
</article>

<section class="band abs" style="top:1195px;height:640px"></section>
<h2 class="section-title" style="top:1254px">Our <b>Categories</b></h2>
<p class="section-sub" style="top:1327px">Verified deals updated daily</p>
<div class="arrow grey" style="left:42px;top:1521px"><svg width="10" height="12"><path d="M7 1L2 6l5 5" stroke="#fff" stroke-width="2" fill="none"/></svg></div>
<div class="arrow blue" style="left:1131px;top:1521px"><svg width="10" height="12"><path d="M3 1l5 5-5 5" stroke="#fff" stroke-width="2" fill="none"/></svg></div>
<div class="cat-card abs" style="left:111px"><div class="cat-img" role="img" aria-label="Terrier eating from a metal bowl on a rug" style="background:linear-gradient(160deg,#c7b79c,#8f7b63 60%,#cfc2ad)"></div><h3>Dog Food</h3></div>
<div class="cat-card abs" style="left:448px"><div class="cat-img" role="img" aria-label="Corgi resting in a grey bed with rope toys and balls" style="background:linear-gradient(160deg,#e9ebe8,#c9c9c6 55%,#5f6264)"></div><h3>Dog Toys</h3></div>
<div class="cat-card abs" style="left:784px"><div class="cat-img" role="img" aria-label="Beagle running on a grassy trail with its owner" style="background:linear-gradient(180deg,#a9bfd0,#8ea286 50%,#6f8b43)"></div><h3>Dog Health</h3></div>

<h2 class="section-title" style="top:1870px">Popular <b>Stores</b></h2>
<div class="arrow grey" style="left:42px;top:1998px"><svg width="10" height="12"><path d="M7 1L2 6l5 5" stroke="#fff" stroke-width="2" fill="none"/></svg></div>
<div class="arrow blue" style="left:1131px;top:1998px"><svg width="10" height="12"><path d="M3 1l5 5-5 5" stroke="#fff" stroke-width="2" fill="none"/></svg></div>
<div class="store abs" style="left:110px;color:#c4202a">Halvern</div>
<div class="store abs" style="left:310px;color:#d8232a"><i style="background:#d8232a"></i>Brightkit</div>
<div class="store abs" style="left:508px;color:#107c10"><i style="background:#107c10;border-radius:50%"></i>Pixelforge</div>
<div class="store abs" style="left:708px;color:#222">Corvane</div>
<div class="store abs" style="left:908px;color:#d3232a"><i style="background:#d3232a"></i>Tumbleway</div>
<div class="view-all btn-yellow abs">View All</div>

<section class="band abs" style="top:2233px;height:477px"></section>
<h2 class="section-title" style="top:2295px">What Our Happy Pet <b>Parents Are Saying</b></h2>
<div class="arrow grey" style="left:42px;top:2484px"><svg width="10" height="12"><path d="M7 1L2 6l5 5" stroke="#fff" stroke-width="2" fill="none"/></svg></div>
<div class="arrow blue" style="left:1131px;top:2484px"><svg width="10" height="12"><path d="M3 1l5 5-5 5" stroke="#fff" stroke-width="2" fill="none"/></svg></div>
<article class="review abs" style="left:111px">
  <div class="avatar abs" role="img" aria-label="Portrait of reviewer Lena"></div>
  <div class="name abs">Lena R.,</div>
  <div class="lead abs">Easy to use and always up-to-date!</div>
  <div class="rating abs"><i></i>★★★★★</div>
  <div class="quote-mark abs">”</div>
  <p class="text abs" style="top:128px">“I stumbled upon SnoutSaver while searching for discounts on dog treats. Not only did I find a 30% off coupon for Max's favorite brand, but the process was seamless. Now, I check SnoutSaver weekly before any pet purchase!”</p>
</article>
<article class="review abs" style="left:620px">
  <div class="avatar abs" role="img" aria-label="Portrait of reviewer Marco" style="background:linear-gradient(135deg,#c9d4de,#5d7d9c)"></div>
  <div class="name abs">Marco T.,</div>
  <div class="lead abs">A lifesaver for budget-conscious pet owners!</div>
  <div class="rating abs"><i></i>★★★★★</div>
  <div class="quote-mark abs">”</div>
  <p class="text abs" style="top:126px">I love how user-friendly SnoutSaver is. The coupons are always current, and the 'Copy Code' feature is so convenient. It's my go-to site before any pet-related purchase.”</p>
</article>

<h2 class="section-title" style="top:2772px">Latest <b>Deals</b></h2>
<div class="arrow grey" style="left:42px;top:3031px"><svg width="10" height="12"><path d="M7 1L2 6l5 5" stroke="#fff" stroke-width="2" fill="none"/></svg></div>
<div class="arrow blue" style="left:1131px;top:3031px"><svg width="10" height="12"><path d="M3 1l5 5-5 5" stroke="#fff" stroke-width="2" fill="none"/></svg></div>

<div class="deal-img abs" style="left:115px"><div class="deal-pct abs"><i></i>25%</div><div class="deal-tag abs">Sale</div><div class="deal-art abs" role="img" aria-label="Bowl of kibble with bone biscuits" style="background:radial-gradient(ellipse,#d9a455,#b6823a 55%,transparent 72%)"></div></div>
<div class="deal-img abs" style="left:363px"><div class="deal-pct abs"><i></i>25%</div><div class="deal-tag abs">Deals</div><div class="deal-art abs" role="img" aria-label="Grooming brush, shampoo bottle and towel" style="background:radial-gradient(ellipse,#f1e6c4,#d9c28c 55%,transparent 72%)"></div></div>
<div class="deal-img active abs" style="left:610px"><div class="deal-pct abs"><i></i>50%</div>
  <div class="deal-icons abs"><span><svg width="14" height="12"><path d="M7 11L1.5 5.5A3 3 0 017 2a3 3 0 015.5 3.5z" fill="#e0262e"/></svg></span><span><svg width="12" height="12"><rect x="2" y="4" width="8" height="7" fill="#aaa"/></svg></span><span><svg width="14" height="10"><ellipse cx="7" cy="5" rx="6" ry="4" stroke="#aaa" fill="none"/><circle cx="7" cy="5" r="1.6" fill="#aaa"/></svg></span></div>
  <div class="deal-art abs" role="img" aria-label="Three colourful bags of dog food" style="background:linear-gradient(90deg,#e8a43a,#2f8fc4 50%,#d2583a)"></div></div>
<div class="deal-img abs" style="left:858px"><div class="deal-pct abs"><i></i>10%</div><div class="deal-tag abs">Sale</div><div class="deal-art abs" role="img" aria-label="Pink personalised dog collar" style="background:radial-gradient(ellipse,#e2a9da,#c88acb 50%,transparent 72%)"></div></div>

<div class="deal-info abs" style="left:110px"><h4>Wagly Online</h4><div class="kind">Combo Deals &amp; Discounts</div><div class="stars">★★★★★</div><div class="price">$20.00<s>$40.00</s></div></div>
<div class="deal-info abs" style="left:358px"><h4>Cartly</h4><div class="kind">Budget-Friendly Pet Supplies</div><div class="stars">★★★★★</div><div class="price">$50.00<s>$40.00</s></div></div>
<div class="deal-info abs" style="left:605px"><h4>Tailwise Living</h4><div class="kind">Clearance Sale</div><div class="stars">★★★★★</div><div class="price">$55.00<s>$40.00</s></div></div>
<div class="deal-info abs" style="left:854px"><h4>Clever Pet Shopper</h4><div class="kind">Top Deals</div><div class="stars">★★★★★</div><div class="price">$15.00<s>$40.00</s></div></div>
<div class="view-deals btn-yellow abs">View All Deals</div>

<footer class="site-footer abs">
  <div class="f-brand abs"><span class="brand-mark"></span><span>Snout <b>Saver</b></span></div>
  <div class="socials abs"><span></span><span></span><span></span></div>
  <div class="f-col abs" style="left:420px"><h5>Quick Links</h5><ul><li>Home</li><li>Coupon Cards</li><li>Categories</li><li>Popular Stores</li><li>Latest Deals</li></ul></div>
  <div class="f-col abs" style="left:634px"><h5>Popular Categories</h5><ul><li>Dog Food &amp; Treats</li><li>Toys &amp; Accessories</li><li>Health &amp; Grooming</li><li>Training &amp; Services</li><li>Outdoor &amp; Travel</li></ul></div>
  <div class="f-col contact abs" style="left:875px"><h5>Contact Us</h5><ul>
    <li><span class="ci"><svg width="12" height="12"><path d="M2 1h3l1 3-2 1a7 7 0 003 3l1-2 3 1v3c-6 0-10-4-10-9z" fill="#fff"/></svg></span>+1 555 010 2468</li>
    <li><span class="ci"><svg width="12" height="10"><rect x=".5" y=".5" width="11" height="9" stroke="#fff" fill="none"/><path d="M1 1l5 4 5-4" stroke="#fff" fill="none"/></svg></span>info@snoutsaver.net</li>
    <li><span class="ci"><svg width="10" height="13"><path d="M5 12S1 7 1 4.5a4 4 0 018 0C9 7 5 12 5 12z" fill="#fff"/></svg></span>Orchard Lane. 28 Orchard Ln,<br>Brookfield, NY 10099,</li>
  </ul></div>
  <div class="f-rule abs"></div>
  <p class="copyright abs">Copyright © 2025 Snout Saver. All rights reserved.</p>
</footer>

</div>
</body>
</html>
```